Luxury Wine Label for New Startup Winery

We need a wine label for our new winery startup. We have worked with a local designer but do not feel the resulting label / logo have the elevation required to present our brand as a luxury wine. Our winery is called "Quailbrook Vineyards" and we are focused on extremely high quality hand crafted artisan and estate wines from the Pacific Northwest.
We would like to see designs that utilize a tree line, or other imagery that represents the "Quailbrook" part of our company name. Another interesting feature could be wood grain.
A logo will be required based on your design so please design with this in mind:
This logo should be consistent with the wine bottle label design, and should be representative of our high end exclusive wine while giving a sense of place (Oregon/ Pacific Northwest.)
I will supply an image of the design we received from our local designer, PLEASE NOTE: in general we do like wood grain and tree line concepts but feel the execution was poorly done.
ATTN: Logo design should be suitable for use on: Bottles (Red wine/rose/white wine), Bussiness cards, vehicle signage, business signage, etc
P.S.:
If you have a design that is not outside the box we are still interested in seeing it.
Label is for a burgundy style bottle with a label height of 3.5 - 4" and a width of 3.5-4"
any label <= 4"x4" and >=3.5"x3.5" will be acceptable:
HOWEVER Width should be greater than or equal to height due to the bottle format
Target Market(s)
Wine enthusiasts with adequate discretionary budgets to afford $100 bottles of wine.
Industry/Entity Type
Wine / Winery
Requirements
Must have
- A sense of luxury, a feel of exclusivity, and a theme consistent with our product and brand name
Nice to have
- Tree line, wood grain or other wood themes. Serif fonts
Should not have
- anything cheesy, off topic, hard to read script fonts or anything that makes the label hard to read from a few feet away or too busy

```html
<!DOCTYPE html>
<html lang="en">
<head>
<meta charset="utf-8">
<title>Quailbrook Vineyards – Syrah Label</title>
<link rel="stylesheet" href="https://fonts.googleapis.com/css2?family=IM+Fell+English+SC&display=swap">
<style>
  :root {
    --page-bg: #2b2b2d;
    --label-black: #050607;
    --rule-grey: #8d8e92;
    --gold-light: #f5dc55;
    --gold-mid: #d8b945;
    --gold-muted: #c9b27a;
    --wood-dark: #3a1f10;
    --wood-mid: #6b3a1c;
    --wood-light: #8a4e26;
    --serif: "IM Fell English SC", "Times New Roman", serif;
  }
  * { margin: 0; padding: 0; box-sizing: border-box; }
  html, body {
    width: 1200px; height: 922px; overflow: hidden;
    background: var(--page-bg);
  }
  .label-set {
    position: absolute; left: 192px; top: 28px; width: 815px;
  }
  .front-label {
    position: relative; width: 815px; height: 662px;
    background: var(--label-black);
  }
  .front-label__rule {
    position: absolute; left: 0; right: 0; height: 2px;
    background: var(--rule-grey);
  }
  .front-label__rule--top { top: 50px; }
  .front-label__rule--bottom { top: 611px; }
  .landscape-art {
    position: absolute; left: 0; top: 78px; width: 815px; height: 312px;
    background:
      radial-gradient(ellipse 70% 40% at 50% 88%, rgba(216,185,69,0.55), rgba(216,185,69,0) 70%),
      linear-gradient(180deg, rgba(201,178,122,0.12) 0%, rgba(216,185,69,0.28) 70%, rgba(5,6,7,0) 100%);
  }
  .gold-text {
    background: linear-gradient(90deg, var(--gold-light) 0%, var(--gold-mid) 45%, var(--gold-muted) 100%);
    -webkit-background-clip: text; background-clip: text;
    color: transparent;
  }
  .brand-name {
    position: absolute; left: 0; right: 0; top: 362px;
    text-align: center; font-family: var(--serif); font-weight: 400;
    font-size: 74px; line-height: 76px; letter-spacing: 6px;
  }
  .region-name {
    position: absolute; left: 0; right: 0; top: 518px;
    text-align: center; font-family: var(--serif);
    font-size: 56px; line-height: 60px; letter-spacing: 2px;
  }
  .varietal-band {
    position: relative; width: 815px; height: 179px; margin-top: 25px;
  }
  .wood-grain {
    position: absolute; inset: 0;
    background: linear-gradient(90deg, var(--wood-dark) 0%, var(--wood-mid) 18%, var(--wood-light) 35%, var(--wood-mid) 55%, var(--wood-light) 75%, var(--wood-dark) 100%);
  }
  .varietal-band__rule {
    height: 3px; background: var(--gold-light);
  }
  .varietal-band__rule--top {
    position: absolute; left: 0; right: 0; top: 50px;
  }
  .varietal-name {
    position: absolute; left: 0; right: 0; top: 62px;
    text-align: center; font-family: var(--serif); font-weight: 400;
    font-size: 46px; line-height: 50px; letter-spacing: 30px; padding-left: 30px;
  }
  .vintage-row {
    position: absolute; left: 0; right: 0; top: 110px; height: 34px;
    display: flex; align-items: center; gap: 10px;
  }
  .vintage-row .varietal-band__rule { flex: 1 1 auto; }
  .vintage-line {
    flex: 0 0 auto;
    font-family: var(--serif);
    font-size: 30px; line-height: 34px; letter-spacing: 1px;
    white-space: nowrap;
  }
</style>
</head>
<body>
  <main class="label-set">
    <section class="front-label">
      <div class="front-label__rule front-label__rule--top"></div>
      <div class="landscape-art" role="img" aria-label="Gold line illustration of mountain peaks above a silhouetted tree line"></div>
      <h1 class="brand-name gold-text">QUAILBROOK<br>VINEYARDS</h1>
      <p class="region-name gold-text">Willamette Valley</p>
      <div class="front-label__rule front-label__rule--bottom"></div>
    </section>
    <section class="varietal-band">
      <div class="wood-grain" role="img" aria-label="Dark walnut wood grain texture"></div>
      <div class="varietal-band__rule varietal-band__rule--top"></div>
      <h2 class="varietal-name gold-text">SYRAH</h2>
      <div class="vintage-row">
        <div class="varietal-band__rule"></div>
        <p class="vintage-line gold-text">ESTATE | 2023 | GROWN</p>
        <div class="varietal-band__rule"></div>
      </div>
    </section>
  </main>
</body>
</html>
```